design an extra page for our profile

we are looking for someone to create another page like the attached but with the below changes:
heading changed to (Construction)
icons changed and names to reflect new services i.e
- Residential Building
- Commercial Building
- Landscaping
- Concrete
- Painting

the very bottom of the page is to stay the same with our office info

```html
<!DOCTYPE html>
<html lang="en">
<head>
<meta charset="utf-8">
<title>Construction – Kestrel Services</title>
<link rel="stylesheet" href="https://fonts.googleapis.com/css2?family=Montserrat:wght@700;800&family=Didact+Gothic&display=swap">
<style>
  :root {
    --brand-blue: #0b6fb8;
    --sky-top: #0b72b9;
    --sky-mid: #3f8fcb;
    --sky-pale: #a4c8e6;
    --haze: #eef4f9;
    --white: #ffffff;
    --skyline-dark: #1e1e1e;
    --reflection-warm: #a58a6e;
    --reflection-blue: #8fb2d8;
  }
  * { margin: 0; padding: 0; box-sizing: border-box; }
  html, body { width: 969px; height: 1200px; overflow: hidden; background: var(--white); }
  .page {
    position: absolute; left: 92px; top: 93px; width: 784px; height: 1015px;
    overflow: hidden;
    background: linear-gradient(180deg, var(--sky-top) 0, var(--sky-mid) 270px, var(--sky-pale) 470px, var(--haze) 620px, #f7f9fb 700px);
  }
  .title {
    position: absolute; left: 0; right: 0; top: 76px; text-align: center;
    font: 800 49px/1 "Montserrat", sans-serif; color: var(--white); letter-spacing: 0.5px;
  }
  .title-rule { position: absolute; left: 203px; width: 378px; top: 134px; height: 7px; background: var(--white); }
  .intro {
    position: absolute; left: 0; right: 0; top: 166px; text-align: center;
    font: 400 15px/32.5px "Didact Gothic", sans-serif; color: var(--white); letter-spacing: 1.6px;
  }
  .service { position: absolute; text-align: center; color: var(--brand-blue); }
  .service svg { display: block; margin: 0 auto; fill: var(--brand-blue); }
  .service-name { margin-top: 10px; font: 800 17px/22px "Montserrat", sans-serif; }
  .divider { position: absolute; width: 0; border-left: 2px dotted var(--brand-blue); }
  .skyline-art {
    position: absolute; left: 0; right: 0; top: 671px; height: 240px;
    background: linear-gradient(180deg, rgba(255,255,255,0) 0, #e4e7ea 12%, #4a4a4a 32%, var(--skyline-dark) 58%, var(--reflection-warm) 59%, #9aa7b8 80%, var(--reflection-blue) 100%);
  }
  .footer {
    position: absolute; left: 0; right: 0; top: 911px; bottom: 0;
    background: linear-gradient(180deg, var(--reflection-blue) 0, var(--brand-blue) 100%);
  }
  .brand {
    position: absolute; left: 30px; top: 952px; width: 116px; text-align: center;
    font: 700 21px/1 "Montserrat", sans-serif; color: var(--white); letter-spacing: 0.5px;
  }
  .contact {
    position: absolute; left: 158px; width: 590px; color: var(--white);
    font: 400 16px/1 "Didact Gothic", sans-serif; white-space: nowrap;
  }
  .contact strong { font-family: "Montserrat", sans-serif; font-weight: 700; font-size: 15px; }
  .office { top: 930px; text-align: center; }
  .contact-rule { position: absolute; left: 158px; width: 590px; top: 961px; height: 1px; background: var(--white); }
  .web { top: 965px; display: flex; justify-content: space-between; align-items: baseline; gap: 12px; font-size: 15px; }
  .web strong { font-size: 13px; }
</style>
</head>
<body>
<main class="page">
  <h1 class="title">CONSTRUCTION</h1>
  <div class="title-rule"></div>
  <p class="intro">AS NEW TENANTS TO THE BUILDING AND AS A WAY OF<br>INTRODUCING OURSELVES WE WOULD LIKE TO OFFER A 10%<br>DISCOUNT ON ANY OF BELOW SERVICES.</p>

  <div class="service" style="left:117px;top:358px;width:120px">
    <svg width="92" height="76" viewBox="0 0 92 76">
      <path d="M0 12 L36 2 L46 8 V76 H0 Z M44 22 L70 16 L80 22 L80 40 L92 54 V76 H88 V56 L76 42 V76 H44 Z"/>
      <g fill="#fff"><rect x="5" y="16" width="5" height="7"/><rect x="15" y="14" width="5" height="7"/><rect x="25" y="12" width="5" height="7"/><rect x="5" y="30" width="5" height="7"/><rect x="15" y="30" width="5" height="7"/><rect x="25" y="30" width="5" height="7"/><rect x="5" y="44" width="5" height="7"/><rect x="15" y="44" width="5" height="7"/><rect x="25" y="44" width="5" height="7"/><rect x="50" y="34" width="4" height="6"/><rect x="58" y="32" width="4" height="6"/><rect x="66" y="30" width="4" height="6"/><rect x="50" y="46" width="4" height="6"/><rect x="58" y="46" width="4" height="6"/><rect x="66" y="46" width="4" height="6"/></g>
    </svg>
    <div class="service-name">RESIDENTIAL<br>BUILDING</div>
  </div>
  <div class="divider" style="left:286px;top:349px;height:136px"></div>

  <div class="service" style="left:322px;top:350px;width:140px">
    <svg width="74" height="84" viewBox="0 0 74 84">
      <path d="M22 18 L56 0 V80 H72 V84 H0 V80 H2 V34 L40 24 L48 30 V80 H22 Z"/>
      <g fill="#fff"><rect x="10" y="44" width="28" height="5"/><rect x="10" y="54" width="28" height="5"/><rect x="10" y="64" width="28" height="5"/><rect x="10" y="74" width="28" height="4"/></g>
    </svg>
    <div class="service-name">COMMERCIAL<br>BUILDING</div>
  </div>
  <div class="divider" style="left:498px;top:349px;height:136px"></div>

  <div class="service" style="left:524px;top:364px;width:130px">
    <svg width="78" height="72" viewBox="0 0 78 72">
      <circle cx="19" cy="12" r="7"/><circle cx="19" cy="20" r="9"/><rect x="17" y="26" width="4" height="10"/>
      <circle cx="62" cy="8" r="7"/><circle cx="62" cy="17" r="10"/><rect x="60" y="26" width="4" height="14"/>
      <path d="M0 34 H14 L40 42 C28 46 12 56 4 66 H0 Z M8 70 C24 48 52 38 78 40 V72 H8 Z"/>
    </svg>
    <div class="service-name">LANDSCAPING</div>
  </div>

  <div class="service" style="left:226px;top:529px;width:120px">
    <svg width="60" height="64" viewBox="0 0 60 64">
      <rect x="0" y="0" width="22" height="6" rx="3" transform="rotate(30 0 0)"/>
      <path d="M20 12 L30 10 L56 32 L24 32 Z"/>
      <path d="M6 34 L38 26 L60 38 V48 L32 64 L6 48 Z"/>
      <path fill="#fff" d="M12 38 L36 32 L52 40 L30 48 Z" opacity="0.9"/>
    </svg>
    <div class="service-name">CONCRETE</div>
  </div>
  <div class="divider" style="left:392px;top:517px;height:99px"></div>

  <div class="service" style="left:443px;top:529px;width:120px">
    <svg width="80" height="64" viewBox="0 0 80 64">
      <path d="M2 8 H10 V4 H16 V8 H22 V2 H28 V8 H36 V18 H2 Z"/>
      <rect x="0" y="22" width="38" height="8" rx="2"/>
      <path d="M38 26 H42 V36 H22 V40 H18 V32 H38 Z"/>
      <path d="M14 40 H26 L22 46 V64 H18 V46 Z"/>
      <path d="M46 26 C46 12 74 12 74 26 H71 C71 16 49 16 49 26 Z"/>
      <path d="M44 26 H76 L72 64 H48 Z"/>
      <path fill="#fff" d="M52 32 H68 L66 52 C62 46 58 48 55 52 Z"/>
    </svg>
    <div class="service-name">PAINTING</div>
  </div>

  <div class="skyline-art" role="img" aria-label="Illustrated harbour city skyline with opera house silhouette, sunburst, birds and water reflection beneath clouds"></div>

  <footer class="footer"></footer>
  <div class="brand">KESTREL</div>
  <p class="contact office"><strong>HOME OFFICE:</strong> 1300 555 019 Suite 2.04, 18 Harbourline Way Norwest</p>
  <div class="contact-rule"></div>
  <p class="contact web"><strong>WWW.KESTREL-SERVICES.COM.AU</strong><span>SYDNEY | CANBERRA | BRISBANE | MELBOURNE</span></p>
</main>
</body>
</html>
```